Banner Design for Brisk Loans

Hi,

I know this is under flyer design, however, I am actually after a Banner (I could not find this option). The banner needs to be done to fit the following specifications.

1 x 850mm W x 1500mm H Double Sided Luxury Retractable

I have provided a banner which I currently have however, I would like it to be updated.

I would like to banners created.

Banner 1

The banner should still maintain the lender logos and the fact we assess over 30 lenders, plus also promote the 'Brisk Loans' logo.

Along with this is I would like to promote the 'Brisk Cost Refund.'

Also have the wording
'We Cover your Discharge fee and new loan application fee'
also may use this link as guidance http://www.briskloans-demo.com.au/briskcostrefund/

Banner 2

This banner I would like it to promote a 'Quick Mortgage Health Check'.

Also include 'The Brisk Loans Edge'

http://www.briskloans-demo.com.au/briskcostrefund/

Again use this as a guide as to the 4 points of difference, you may use different icons if you feel it looks better

Target Market(s)

People with Home Loans

Industry/Entity Type

Finance

Font styles to use
Sans Serif

Colors
ec1f27
ffffff

Requirements
Must have
• As per the description
Nice to have
• Professional look, good icons to accompany wording
Should not have
• unprofessional look too much text or cluttered

```html
<!DOCTYPE html>
<html lang="en">
<head>
<meta charset="utf-8">
<title>Brisk Loans – Brisk Cost Refund Banner</title>
<link rel="stylesheet" href="https://fonts.googleapis.com/css2?family=Cinzel:wght@600;700&family=Oswald:wght@500;600;700&family=Anton&family=Open+Sans:wght@700&display=swap">
<style>
  :root {
    --brand-red: #ec1f27;
    --deep-red: #c8141b;
    --ink: #1f1f1f;
    --charcoal: #2e2e2e;
    --slate: #555555;
    --white: #ffffff;
    --paper: #f6f6f6;
    --stage: #d9dcdf;
  }
  * { box-sizing: border-box; margin: 0; padding: 0; }
  html, body { width: 768px; height: 1200px; overflow: hidden; background: var(--stage); }
  .banner {
    position: relative; width: 768px; height: 1200px; overflow: hidden;
    background: linear-gradient(180deg, var(--white) 0%, var(--paper) 100%);
    text-align: center;
  }
  .brand { position: absolute; top: 150px; left: 0; right: 0; }
  .brand-mark { display: inline-flex; align-items: center; gap: 18px; }
  .brand-square { width: 46px; height: 46px; background: var(--brand-red); }
  .brand-name {
    font-family: "Cinzel", serif; font-weight: 700; font-size: 66px;
    color: var(--ink); letter-spacing: 1px; line-height: 1.1;
  }
  .brand-tagline {
    margin-top: 10px; font-family: "Cinzel", serif; font-weight: 700;
    font-size: 19px; color: var(--ink); letter-spacing: .5px;
  }
  .divider {
    position: absolute; top: 356px; left: 130px; width: 508px; height: 2px;
    background: linear-gradient(90deg, transparent, #bdbdbd, transparent);
  }
  .headline { position: absolute; top: 376px; left: 0; right: 0; line-height: 1; }
  .headline-top { display: flex; justify-content: center; align-items: baseline; gap: 22px; }
  .headline-brand { font-family: "Cinzel", serif; font-weight: 700; font-size: 80px; color: var(--ink); }
  .headline-red { font-family: "Anton", sans-serif; font-size: 84px; color: var(--brand-red); letter-spacing: 1px; }
  .headline-bottom {
    display: block; margin-top: 10px; font-family: "Anton", sans-serif; font-size: 84px;
    color: var(--brand-red); letter-spacing: 1px;
  }
  .cover-box {
    position: absolute; top: 648px; left: 34px; width: 700px; height: 164px;
    background: linear-gradient(180deg, #4a4a4a 0%, var(--charcoal) 60%, #1a1a1a 100%);
    border: 4px solid var(--brand-red);
    box-shadow: 0 10px 18px rgba(0,0,0,.25);
    padding-top: 40px;
  }
  .cover-tab {
    position: absolute; top: 612px; left: 218px; width: 332px; height: 64px;
    background: var(--brand-red); border-radius: 8px;
    font-family: "Open Sans", sans-serif; font-weight: 700; font-size: 40px;
    color: var(--white); line-height: 64px; letter-spacing: 1px;
    box-shadow: 0 4px 8px rgba(0,0,0,.3);
  }
  .cover-text {
    font-family: "Oswald", sans-serif; font-weight: 600; font-size: 44px;
    line-height: 1.1; color: var(--white); text-transform: uppercase; letter-spacing: .5px;
  }
  .lenders-band {
    position: absolute; top: 844px; left: 0; right: 0; height: 60px;
    background: linear-gradient(180deg, var(--brand-red), var(--deep-red));
    font-family: "Cinzel", serif; font-weight: 700; font-size: 28px;
    color: var(--white); line-height: 60px; letter-spacing: 1px;
  }
  .lender-grid {
    position: absolute; top: 930px; left: 28px; right: 28px; list-style: none;
    display: grid; grid-template-columns: repeat(5, 1fr); row-gap: 30px; align-items: center;
  }
  .lender {
    display: flex; align-items: center; justify-content: center; gap: 6px;
    font-family: "Oswald", sans-serif; font-weight: 500; font-size: 19px; color: var(--slate);
    white-space: nowrap;
  }
  .lender-dot { width: 12px; height: 12px; border-radius: 50%; background: var(--brand-red); }
  .web-footer { position: absolute; left: 0; right: 0; bottom: 0; height: 92px; }
  .web-footer svg { position: absolute; inset: 0; }
  .web-address {
    position: absolute; left: 0; right: 0; top: 26px;
    font-family: "Cinzel", serif; font-weight: 700; font-size: 28px;
    color: var(--white); letter-spacing: 1px;
  }
</style>
</head>
<body>
<main class="banner">
  <header class="brand">
    <div class="brand-mark">
      <span class="brand-square"></span>
      <span class="brand-name">Brisk Loans</span>
    </div>
    <p class="brand-tagline">IS YOUR HOME LOAN IN TOP FORM?</p>
  </header>

  <div class="divider"></div>

  <h1 class="headline">
    <span class="headline-top">
      <span class="headline-brand">Brisk</span>
      <span class="headline-red">COST</span>
    </span>
    <span class="headline-bottom">REFUND</span>
  </h1>

  <section class="cover-box">
    <p class="cover-text">Your discharge fee and<br>new loan application fee</p>
  </section>
  <div class="cover-tab">WE COVER</div>

  <div class="lenders-band">WE ASSESS OVER 30 LENDERS</div>

  <ul class="lender-grid">
    <li class="lender">Ivory Direct</li>
    <li class="lender">Westvale</li>
    <li class="lender"><span class="lender-dot"></span>Mesa Bank</li>
    <li class="lender">Sunridge Bank</li>
    <li class="lender">Wattle</li>
    <li class="lender">Harbour Mutual</li>
    <li class="lender">Civic Bank</li>
    <li class="lender">Homestead</li>
    <li class="lender">Paprika</li>
    <li class="lender">Plot Lending</li>
    <li class="lender">Corella Bank</li>
    <li class="lender">Arbor Bank</li>
    <li class="lender">Azure</li>
    <li class="lender">Nordic</li>
    <li class="lender">Legacy Bank</li>
  </ul>

  <footer class="web-footer">
    <svg width="768" height="92" viewBox="0 0 768 92" aria-hidden="true">
      <polygon points="0,92 40,0 728,0 768,92" fill="#ec1f27"/>
      <polygon points="0,92 40,0 0,40" fill="#1f1f1f"/>
      <polygon points="768,92 728,0 768,40" fill="#1f1f1f"/>
    </svg>
    <p class="web-address">WWW.BRISKLOANS-DEMO.COM.AU</p>
  </footer>
</main>
</body>
</html>
```